Marwick Law Letterhead

We need a new letterhead design for a Law Firm. The address for the law firm is 1475 Calloway Street, Suite 210, Houston, Texas 77041. Phone Number: 832-361-9027; Fax Number: 832-614-7359. The logo is uploaded to the project.

```html
<!DOCTYPE html>
<html lang="en">
<head>
<meta charset="utf-8">
<title>Marwick Law Letterhead</title>
<link href="https://fonts.googleapis.com/css2?family=Arimo:wght@400;700&family=Tinos:wght@400;700&display=swap" rel="stylesheet">
<style>
  :root {
    --navy: #1c2f5e;
    --red: #a3161c;
    --red-dark: #7a1014;
    --ink: #1a1a1a;
    --paper: #ffffff;
    --backdrop: #e9e6e2;
    --sig: #d9d9de;
  }
  * { margin: 0; padding: 0; box-sizing: border-box; }
  html, body { width: 1200px; height: 900px; overflow: hidden; background: var(--backdrop); }
  .letterhead {
    position: absolute; left: 267px; top: 20px;
    width: 665px; height: 860px;
    background: var(--paper);
    box-shadow: 0 4px 18px rgba(0,0,0,.18);
    font-family: "Arimo", Arial, sans-serif;
    color: var(--ink);
  }
  .edge-band { position: absolute; right: 0; top: 0; width: 20px; height: 860px; }
  .brand {
    position: absolute; left: 69px; top: 48px;
    display: flex; align-items: center; gap: 12px;
  }
  .brand-mark { width: 30px; height: 30px; background: var(--navy); }
  .brand-name { font-weight: 700; font-size: 26px; color: var(--navy); letter-spacing: .5px; }
  .letter { position: absolute; left: 69px; width: 528px; font-size: 13.3px; line-height: 20.7px; }
  .date { top: 158px; }
  .recipient { top: 210px; }
  .recipient-name { font-weight: 700; font-size: 14.5px; }
  .body-copy { top: 335px; }
  .body-copy p { text-align: justify; }
  .body-copy p + p { margin-top: 20.7px; }
  .body-copy .salutation + p { margin-top: 0; }
  .body-copy .closing { margin-top: 0; }
  .signature {
    position: absolute; left: 69px; top: 662px;
    width: 86px; height: 22px; background: var(--sig); border-radius: 3px;
  }
  .signer { position: absolute; left: 69px; top: 690px; font-size: 15.5px; }
  .contact {
    position: absolute; left: 69px; top: 794px;
    list-style: none;
    font-family: "Tinos", "Times New Roman", serif;
    font-size: 9.6px; letter-spacing: .8px; color: var(--navy); line-height: 16.5px;
  }
  .contact li { display: flex; align-items: center; gap: 5px; }
  .contact svg { width: 9px; height: 9px; fill: var(--red); }
</style>
</head>
<body>
<main class="letterhead">
  <svg class="edge-band" viewBox="0 0 20 860" preserveAspectRatio="none" aria-hidden="true">
    <rect x="0" y="0" width="20" height="860" fill="var(--navy)"/>
    <polygon points="20,350 20,356 6,380 6,378" fill="#fff"/>
    <polygon points="20,362 20,612 6,636 6,386" fill="var(--red)"/>
    <polygon points="20,362 20,420 6,444 6,386" fill="var(--red-dark)"/>
    <polygon points="20,612 20,618 6,642 6,636" fill="#fff"/>
    <rect x="0" y="0" width="6" height="380" fill="#fff"/>
    <rect x="0" y="636" width="6" height="224" fill="#fff"/>
    <rect x="6" y="720" width="6" height="140" fill="#d8d8dc"/>
  </svg>

  <header class="brand">
    <span class="brand-mark"></span>
    <span class="brand-name">Marwick Law</span>
  </header>

  <p class="letter date">4th September 20XX</p>

  <address class="letter recipient" style="font-style:normal">
    <div class="recipient-name">Ronny Reader</div>
    <div>CEO, Company Name</div>
    <div>123 Address St</div>
    <div>Anytown, ST 12345</div>
  </address>

  <section class="letter body-copy">
    <p class="salutation">Dear Mr. Reader,</p>
    <p>Lorem ipsum dolor sit amet, consectetuer adipiscing elit, sed diam nonummy nibh euismod tincidunt ut laoreet dolore magna aliquam erat volutpat. Ut wisi enim ad minim veniam, quis nostrud exerci tation ullamcorper suscipit lobortis nisl ut aliquip ex ea commodo consequat.</p>
    <p>Duis autem vel eum iriure dolor in hendrerit in vulputate velit esse molestie consequat, vel illum dolore eu feugiat nulla facilisis at vero eros et accumsan.</p>
    <p>Nam liber tempor cum soluta nobis eleifend option congue nihil imperdiet doming id quod mazim placerat facer possim assum. Typi non habent claritatem insitam; est usus legentis in iis qui facit eorum claritatem. Investigationes demonstraverunt lectores legere me lius quod ii legunt saepius.</p>
    <p class="closing">Sincerely,</p>
  </section>

  <div class="signature" role="img" aria-label="Handwritten signature"></div>
  <p class="signer">Your Name</p>

  <ul class="contact">
    <li><svg viewBox="0 0 24 24"><path d="M6.6 10.8a15 15 0 0 0 6.6 6.6l2.2-2.2c.3-.3.7-.4 1-.2 1.1.4 2.3.6 3.6.6.6 0 1 .4 1 1V20c0 .6-.4 1-1 1A17 17 0 0 1 3 4c0-.6.4-1 1-1h3.5c.6 0 1 .4 1 1 0 1.3.2 2.5.6 3.6.1.3 0 .7-.2 1z"/></svg>832-361-9027</li>
    <li><svg viewBox="0 0 24 24"><path d="M6 2h12v6H6zM3 9h18a1 1 0 0 1 1 1v8h-4v4H6v-4H2v-8a1 1 0 0 1 1-1zm5 7v4h8v-4z"/></svg>832-614-7359</li>
    <li><svg viewBox="0 0 24 24"><path d="M12 2a7 7 0 0 0-7 7c0 5 7 13 7 13s7-8 7-13a7 7 0 0 0-7-7zm0 9.5A2.5 2.5 0 1 1 12 6.5a2.5 2.5 0 0 1 0 5z"/></svg>1475 Calloway Street, Suite 210, Houston, Texas 77041</li>
  </ul>
</main>
</body>
</html>
```